Event Website Design

We need a new website design for an events driven website. The domain for this site is http://brackmoorhalls.co.uk. The site is up and running but needs a new fresh, modern look.
I've attached a Balamiq Mockup for the layout of the home page. Also attached is a png of the logo.
Key colours for the site are 0f7e6a, 35bde, d57835 & 373737.
Font to use is Proxima Nova
Width of the site should be 1200px
The design should be contemporary with minimal clutter.
Websites to references are…
http://vorpin.london/
http://www.darvushall.co.uk/
These are just guidelines, please feel free to use you own creative judgment.
The selected design file needs to be supplied as an editable PSD.
Reason: I've submitted 5 designs to the client, who will select the one they want. I will then choose that design. So please be patient as I'm waiting for a decision from my client.
Industry/Entity Type
Events
Number of Pages Required
1 page
Look and feel
Each slider illustrates characteristics of the customer's brand and the style your logo design should communicate.

```html
<!DOCTYPE html>
<html lang="en">
<head>
<meta charset="utf-8">
<title>Brackmoor Halls – Home</title>
<link href="https://fonts.googleapis.com/css2?family=Figtree:ital,wght@0,300;0,400;0,600;0,700;1,400&display=swap" rel="stylesheet">
<style>
:root{
  --green:#0f7e6a;
  --blue:#1f5fd0;
  --orange:#d57835;
  --dark:#373737;
  --darker:#2e2e2e;
  --text:#333333;
  --muted:#777777;
  --light:#f4f4f4;
  --line:#e2e2e2;
  --white:#ffffff;
}
*{box-sizing:border-box;margin:0;padding:0}
html,body{width:1200px;height:2761px;overflow:hidden}
body{font-family:"Figtree",Arial,sans-serif;color:var(--text);background:var(--white);position:relative}
.abs{position:absolute}
a{color:inherit;text-decoration:none}

/* header */
.topbar{top:0;left:0;width:1200px;height:120px;background:var(--dark)}
.brand{left:160px;top:40px;color:var(--white);font-weight:700;font-size:14px;letter-spacing:.5px;display:flex;align-items:center;gap:8px;white-space:nowrap}
.brand-mark{width:14px;height:14px;background:var(--green);flex:none}
.tagline{left:160px;top:88px;color:var(--white);font-size:11px;font-weight:600}
.box-office{left:377px;top:18px;color:var(--white);font-size:17px;font-weight:600;white-space:nowrap}
.util-links{left:592px;top:22px;display:flex;gap:0;font-size:10px;color:#bcbcbc;text-transform:uppercase;font-weight:600;white-space:nowrap}
.util-links span{padding:0 10px;border-left:1px solid #666}
.util-links span:first-child{padding-left:0;border-left:0}
.search{left:592px;top:62px;width:323px;height:38px;border-radius:19px;background:#222;color:#999;font-size:11px;padding:12px 18px}
.search svg{position:absolute;right:14px;top:12px}
.social{top:62px;display:flex;gap:10px;left:928px}
.social i{display:block;width:34px;height:34px;border-radius:50%;background:#242424}

.nav{top:120px;left:0;width:1200px;height:57px;background:var(--white);border-bottom:1px solid var(--line)}
.nav ul{list-style:none;display:flex;position:absolute;left:160px;top:0;height:57px}
.nav li{font-size:13px;font-weight:600;color:#222;padding:0 12px;line-height:57px;border-right:1px solid var(--line);white-space:nowrap}
.nav li:first-child{border-left:1px solid var(--line)}
.stripe{left:0;width:1200px;height:6px;display:flex}
.stripe i{flex:1;display:block}
.stripe i:nth-child(1){background:var(--green)}
.stripe i:nth-child(2){background:var(--orange)}
.stripe i:nth-child(3){background:var(--blue)}

/* hero */
.hero{top:182px;left:0;width:1200px;height:594px;background:radial-gradient(circle at 70% 35%,#a2707a 0%,#5a3b4c 35%,#2a1f2e 75%,#1c1620 100%)}
.hero-title{left:160px;top:190px;color:var(--white);font-size:50px;font-weight:700}
.hero-date{left:160px;top:258px;color:var(--white);font-size:19px;display:flex;align-items:center;gap:8px}
.hero-text{left:160px;top:296px;width:380px;color:var(--white);font-size:15px;font-weight:600;line-height:20px}
.hero-btns{left:160px;top:381px;display:flex;gap:12px}
.btn-solid{display:inline-block;width:100px;height:40px;border-radius:20px;border:2px solid var(--white);color:var(--white);font-size:15px;font-weight:700;text-align:center;line-height:36px}
.btn-solid.green{background:var(--green)}
.btn-solid.orange{background:var(--orange)}
.hero-arrow{top:275px}

/* event cards */
.cards{top:828px;left:160px;display:flex;gap:21px}
.card{width:204px;height:322px;border:1px solid var(--line);background:var(--white)}
.card-img{height:151px}
.card h3{font-size:15px;font-weight:700;margin:27px 0 0 17px}
.card .date{font-size:11px;margin:8px 0 0 17px;display:flex;align-items:center;gap:5px}
.card p{font-size:10px;line-height:14px;margin:8px 17px 0;color:#444}
.card .btns{display:flex;gap:6px;margin:19px 0 0 17px}
.pill{display:inline-block;height:26px;border-radius:13px;border:1.5px solid;font-size:10px;font-weight:700;text-align:center;line-height:23px;background:var(--white)}
.pill.green{border-color:var(--green);color:var(--green)}
.pill.orange{border-color:var(--orange);color:var(--orange)}
.pill.blue{border-color:var(--blue);color:var(--blue)}
.card .pill{width:66px}

/* news */
.news{top:1205px;left:0;width:1200px;height:445px;background:var(--light)}
.news h2{position:absolute;left:0;width:1200px;text-align:center;top:66px;font-size:37px;font-weight:400;color:#222}
.see-all{position:absolute;left:956px;top:82px;font-size:11px;font-weight:700;color:var(--muted)}
.news-item{position:absolute;top:170px;width:250px}
.news-head{display:flex;gap:12px}
.news-date{width:40px;color:var(--green);font-weight:700;text-align:center;border-right:2px solid #cfcfcf;padding-right:8px}
.news-date b{display:block;font-size:14px;line-height:14px}
.news-date strong{display:block;font-size:27px;line-height:26px}
.news-head h3{font-size:18px;font-weight:400;line-height:24px;color:#222}
.news-item p{font-size:10.5px;line-height:16.5px;margin-top:21px;color:#333}
.news-item .pill{width:73px;margin-top:20px;background:transparent}

/* features */
.feature{position:absolute;top:1715px;width:274px;text-align:center}
.feature svg{height:42px}
.feature h3{font-size:23px;font-weight:400;color:#222;margin-top:22px}
.feature-img{height:149px;margin-top:6px}
.feature p{font-size:10.5px;line-height:16.5px;margin:24px 6px 0;color:#333}
.feature .pill{width:73px;margin-top:18px}

/* sports */
.sports{top:2137px;left:0;width:1200px;height:345px;background:linear-gradient(90deg,#5e5e5e 0%,#8a8a88 40%,#6e6560 70%,#9a7a66 100%)}
.sports-box{left:386px;top:95px;width:429px;height:151px;background:rgba(40,40,40,.55);text-align:center;color:var(--white)}
.sports-box h2{font-size:34px;font-weight:300;margin-top:30px}
.sports-box p{font-size:14px;font-style:italic;line-height:19px;margin-top:6px}

/* footer */
.footer{top:2482px;left:0;width:1200px;height:279px;background:var(--dark);color:#cfcfcf}
.footer h4{position:absolute;top:59px;font-size:12px;font-weight:700;color:var(--white);text-transform:uppercase}
.footer ul{list-style:none;position:absolute;top:87px;font-size:11.5px;line-height:18.5px}
.footer address{position:absolute;left:160px;top:85px;font-style:normal;font-size:12px;line-height:22px}
.footer-divider{left:821px;top:50px;width:1px;height:200px;background:#555}
.footer-brand{left:848px;top:72px;color:var(--white);font-size:26px;font-weight:700;letter-spacing:1px;display:flex;align-items:center;gap:10px}
.footer-copy{left:857px;top:166px;font-size:11px;line-height:22px;color:var(--white)}
</style>
</head>
<body>

<header class="abs topbar">
  <div class="abs brand"><span class="brand-mark"></span>BRACKMOOR HALLS</div>
  <div class="abs tagline">WESSEX'S PREMIER Entertainment and Sporting Centre</div>
  <div class="abs box-office">Box Office 01632 960418</div>
  <div class="abs util-links"><span>Gift Voucher</span><span>Join our mailing list</span><span>My Account</span><span>Basket</span><span>Register</span></div>
  <div class="abs search">Search
    <svg width="14" height="14" viewBox="0 0 14 14"><circle cx="6" cy="6" r="4.5" fill="none" stroke="#fff" stroke-width="1.8"/><line x1="9.3" y1="9.3" x2="13" y2="13" stroke="#fff" stroke-width="1.8"/></svg>
  </div>
  <div class="abs social"><i></i><i></i><i></i></div>
</header>

<nav class="abs nav">
  <ul>
    <li>What's On</li><li>Conferencing and Events</li><li>Sports &amp; Leisure</li><li>Meridian Theatre</li><li>Plan Your Visit</li><li>News</li><li>Discover More</li><li>Contact Us</li>
  </ul>
</nav>
<div class="abs stripe" style="top:176px"><i></i><i></i><i></i></div>

<section class="abs hero" role="img" aria-label="Photo of guests celebrating at an evening party with sparklers and lights">
  <h1 class="abs hero-title">Marlo's Party</h1>
  <div class="abs hero-date">
    <svg width="16" height="16" viewBox="0 0 16 16"><rect x="1.5" y="3" width="13" height="11.5" fill="none" stroke="#fff" stroke-width="1.5"/><line x1="1.5" y1="6.5" x2="14.5" y2="6.5" stroke="#fff" stroke-width="1.5"/><line x1="5" y1="1" x2="5" y2="4" stroke="#fff" stroke-width="1.5"/><line x1="11" y1="1" x2="11" y2="4" stroke="#fff" stroke-width="1.5"/></svg>
    Date Dec 28, 2016
  </div>
  <p class="abs hero-text">Sd ut perspiciatis unde omnis isteistenatuvlut atem accuantium doloremque lisut pertisn demis em us antium doloremque liut persciatis un.</p>
  <div class="abs hero-btns"><a class="btn-solid green">MORE</a><a class="btn-solid orange">BOOK</a></div>
  <svg class="abs hero-arrow" style="left:42px" width="26" height="56" viewBox="0 0 26 56"><polyline points="24,2 2,28 24,54" fill="none" stroke="#fff" stroke-width="2"/></svg>
  <svg class="abs hero-arrow" style="left:1128px" width="26" height="56" viewBox="0 0 26 56"><polyline points="2,2 24,28 2,54" fill="none" stroke="#fff" stroke-width="2"/></svg>
</section>

<svg class="abs" style="left:118px;top:893px" width="12" height="20" viewBox="0 0 12 20"><polyline points="10,2 2,10 10,18" fill="none" stroke="#111" stroke-width="2.5"/></svg>
<svg class="abs" style="left:1060px;top:893px" width="12" height="20" viewBox="0 0 12 20"><polyline points="2,2 10,10 2,18" fill="none" stroke="#111" stroke-width="2.5"/></svg>

<section class="abs cards">
  <article class="card">
    <div class="card-img" role="img" aria-label="Photo of a concert crowd under pink stage lights" style="background:linear-gradient(160deg,#c23a7c,#4a1240)"></div>
    <h3>Sed ut perscistis</h3>
    <div class="date"><svg width="10" height="10" viewBox="0 0 16 16"><rect x="1.5" y="3" width="13" height="11.5" fill="none" stroke="#333" stroke-width="2"/></svg>Dec 27, 2016</div>
    <p>Sd ut perspiciatis unde omniiste natuptatem accusantium doe.</p>
    <div class="btns"><a class="pill green">MORE</a><a class="pill orange">BOOK</a></div>
  </article>
  <article class="card">
    <div class="card-img" role="img" aria-label="Photo of an audience applauding" style="background:linear-gradient(160deg,#5f7f99,#2a3a4a)"></div>
    <h3>Sed ut perscistis</h3>
    <div class="date"><svg width="10" height="10" viewBox="0 0 16 16"><rect x="1.5" y="3" width="13" height="11.5" fill="none" stroke="#333" stroke-width="2"/></svg>Dec 27, 2016</div>
    <p>Sd ut perspiciatis unde omniiste natuptatem accusantium doe.</p>
    <div class="btns"><a class="pill green">MORE</a><a class="pill orange">BOOK</a></div>
  </article>
  <article class="card">
    <div class="card-img" role="img" aria-label="Photo of a speaker presenting to a seated audience" style="background:linear-gradient(160deg,#e4e2de,#9b8e80)"></div>
    <h3>Sed ut perscistis</h3>
    <div class="date"><svg width="10" height="10" viewBox="0 0 16 16"><rect x="1.5" y="3" width="13" height="11.5" fill="none" stroke="#333" stroke-width="2"/></svg>Dec 27, 2016</div>
    <p>Sd ut perspiciatis unde omniiste natuptatem accusantium doe.</p>
    <div class="btns"><a class="pill green">MORE</a><a class="pill orange">BOOK</a></div>
  </article>
  <article class="card">
    <div class="card-img" role="img" aria-label="Photo of friends at a night party with string lights" style="background:linear-gradient(160deg,#8a5a3a,#221816)"></div>
    <h3>Sed ut perscistis</h3>
    <div class="date"><svg width="10" height="10" viewBox="0 0 16 16"><rect x="1.5" y="3" width="13" height="11.5" fill="none" stroke="#333" stroke-width="2"/></svg>Dec 27, 2016</div>
    <p>Sd ut perspiciatis unde omniiste natuptatem accusantium doe.</p>
    <div class="btns"><a class="pill green">MORE</a><a class="pill orange">BOOK</a></div>
  </article>
</section>

<section class="abs news">
  <h2>Latest From Brackmoor</h2>
  <a class="see-all">SEE ALL NEWS</a>
  <article class="news-item" style="left:160px">
    <div class="news-head"><div class="news-date"><b>DEC</b><strong>28</strong></div><h3>Sed ut perspiciatisdois iste natussit olupt.</h3></div>
    <p>Sd ut perspiciatis unde omnis isteiste&nbsp; natus errort vo luptatem accusantium doloremque lisS ut pertis un de omnis isteiste&nbsp; natus Sed ut persluptatem us antium doloremque lisS ut persciatis un.</p>
    <a class="pill green">MORE</a>
  </article>
  <article class="news-item" style="left:475px">
    <div class="news-head"><div class="news-date"><b>DEC</b><strong>28</strong></div><h3>Sed ut perspiciatisdois iste natussit olupt.</h3></div>
    <p>Sd ut perspiciatis unde omnis isteiste&nbsp; natus errort vo luptatem accusantium doloremque lisS ut pertis un de omnis isteiste&nbsp; natus Sed ut persluptatem us antium doloremque lisS ut persciatis un.</p>
    <a class="pill green">MORE</a>
  </article>
  <article class="news-item" style="left:791px">
    <div class="news-head"><div class="news-date"><b>DEC</b><strong>28</strong></div><h3>Sed ut perspiciatisdois iste natussit olupt.</h3></div>
    <p>Sd ut perspiciatis unde omnis isteiste&nbsp; natus errort vo luptatem accusantium doloremque lisS ut pertis un de omnis isteiste&nbsp; natus Sed ut persluptatem us antium doloremque lisS ut persciatis un.</p>
    <a class="pill green">MORE</a>
  </article>
</section>

<section class="feature" style="left:160px">
  <svg width="70" height="42" viewBox="0 0 70 42" fill="var(--green)"><circle cx="17" cy="12" r="7"/><circle cx="53" cy="12" r="7"/><path d="M4 36c0-9 6-14 13-14s13 5 13 14z"/><path d="M40 36c0-9 6-14 13-14s13 5 13 14z"/><circle cx="35" cy="14" r="9"/><path d="M18 40c0-11 8-17 17-17s17 6 17 17z"/></svg>
  <h3>Conferences &amp; Events</h3>
  <div class="feature-img" role="img" aria-label="Photo of a presenter addressing a large conference audience" style="background:linear-gradient(160deg,#c0502a,#5a1c12)"></div>
  <p>Sd ut perspiciatis unde omnis iste natus error sitp tatem accusantium dolormqu e laudan tium, totame maperiam, eaque ipsa quae ab illo inventore.</p>
  <a class="pill green">MORE</a>
</section>
<section class="feature" style="left:464px">
  <svg width="52" height="42" viewBox="0 0 52 42" fill="none" stroke="var(--orange)" stroke-width="3"><path d="M6 4h14l-2 12a5 5 0 0 1-10 0z" fill="var(--orange)"/><line x1="13" y1="21" x2="16" y2="38"/><line x1="10" y1="39" x2="21" y2="37"/><path d="M32 4h14l-2 12a5 5 0 0 1-10 0z" fill="var(--orange)"/><line x1="39" y1="21" x2="36" y2="38"/><line x1="31" y1="37" x2="42" y2="39"/></svg>
  <h3>Parties at Brackmoor</h3>
  <div class="feature-img" role="img" aria-label="Photo of friends raising cocktail glasses in a toast" style="background:linear-gradient(160deg,#d9823a,#6a2414)"></div>
  <p>Sd ut perspiciatis unde omnis iste natus error sitp tatem accusantium dolormqu e laudan tium, totame maperiam, eaque ipsa quae ab illo inventore.</p>
  <a class="pill orange">MORE</a>
</section>
<section class="feature" style="left:766px">
  <svg width="56" height="42" viewBox="0 0 56 42" fill="var(--blue)"><ellipse cx="22" cy="15" rx="19" ry="13"/><path d="M10 25l-4 10 12-7z"/><ellipse cx="38" cy="24" rx="15" ry="10" fill="#fff" stroke="var(--blue)" stroke-width="3"/><path d="M45 32l5 8-11-5z"/></svg>
  <h3>Co-working Hub</h3>
  <div class="feature-img" role="img" aria-label="Photo of a person working on a laptop beside a coffee mug" style="background:linear-gradient(160deg,#f1ece4,#b98a60)"></div>
  <p>Sd ut perspiciatis unde omnis iste natus error sitp tatem accusantium dolormqu e laudan tium, totame maperiam, eaque ipsa quae ab illo inventore.</p>
  <a class="pill blue">MORE</a>
</section>

<section class="abs sports" role="img" aria-label="Photo of a group lifting barbells in a gym">
  <div class="abs sports-box">
    <h2>Sports &amp; Leisure</h2>
    <p>Sd ut perspiciatis unde omnis iste natusit tatum unde<br>omnislorem iste natu unde omnis iste natusit.</p>
  </div>
</section>

<footer class="abs footer">
  <div class="abs stripe" style="top:0"><i></i><i></i><i></i></div>
  <h4 style="left:160px">Postal Address</h4>
  <address>Brackmoor Entertainment<br>VenueHarrowgate Close<br>Dunmere<br>Wessex<br>DN40 7QT</address>
  <div class="abs" style="left:383px;top:50px;width:1px;height:200px;background:#555"></div>
  <h4 style="left:403px">Quick Links</h4>
  <ul style="left:403px"><li>All Shows</li><li>Classical Music</li><li>Childrens</li><li>Comedy</li><li>Dence</li><li>Drama</li><li>Literary Festival</li><li>Music</li></ul>
  <ul style="left:565px;top:89px"><li>Musicals</li><li>Opera</li><li>Pantomime</li><li>Psychics</li><li>Talks</li><li>Variety</li><li>People's Activity</li><li>Access Information</li></ul>
  <ul style="left:699px;top:86px"><li>Plan Your Visit</li><li>News</li><li>Discover More</li><li>Contact Us</li></ul>
  <div class="abs footer-divider"></div>
  <div class="abs footer-brand"><span class="brand-mark" style="width:18px;height:18px"></span>BRACKMOOR</div>
  <div class="abs footer-copy">© 2016 Brackmoor Halls.<br>All Copyrights are Reserved.</div>
</footer>

</body>
</html>
```